Boutique custom software development company needs new business card

Our nearly 20 year old custom software development company would like to better include the fact that we are now providing Bitcoin services. These new services are B2B include education (how to acquire and securely hold Bitcoin) and integrating Bitcoin payments into existing ecommerce sites or other existing systems. Please keep the card clean and simple. Attached is our current design and some other files. vextorial.com

Target Market(s)

businesses owners interested in long term relationship

Industry/Entity Type

Custom software development and Bitcoin

Contact Information for Business Card

Dale Parker, dale@vextorial.com, vextorial.com, (888) 555-VXTRL

Font styles to use
Other font styles liked:
• monospace

Requirements
Must have
• double-sided
Nice to have
• clean and simple
Should not have
• physical address

```html
<!DOCTYPE html>
<html lang="en">
<head>
<meta charset="utf-8">
<title>Vextorial – Business Card</title>
<link rel="stylesheet" href="https://fonts.googleapis.com/css2?family=Montserrat:wght@400;500;600;700;800&display=swap">
<style>
  :root {
    --page-bg: #e4e4e4;
    --card-bg: #d8e2ee;
    --brand-blue: #3f74bc;
    --brand-orange: #f07f22;
    --ink: #3a3a3a;
    --shadow: rgba(0, 0, 0, 0.28);
  }
  * { margin: 0; padding: 0; box-sizing: border-box; }
  html, body {
    width: 1200px;
    height: 900px;
    overflow: hidden;
    background: var(--page-bg);
    font-family: "Montserrat", sans-serif;
  }
  .sheet {
    width: 1200px;
    height: 900px;
    display: flex;
    flex-direction: column;
    align-items: center;
    justify-content: center;
    gap: 50px;
  }
  .card {
    width: 660px;
    height: 377px;
    background: var(--card-bg);
    border-radius: 22px;
    box-shadow: 0 6px 14px var(--shadow);
    position: relative;
  }
  .card--front {
    display: flex;
    flex-direction: column;
    align-items: center;
    justify-content: center;
  }
  .brand {
    display: flex;
    flex-direction: column;
    align-items: flex-start;
  }
  .brand__row {
    display: flex;
    align-items: center;
    gap: 12px;
  }
  .brand__square {
    width: 30px;
    height: 30px;
    background: var(--brand-orange);
  }
  .brand__name {
    font-weight: 800;
    color: var(--brand-blue);
    font-size: 58px;
    letter-spacing: 1px;
    line-height: 1;
    text-transform: uppercase;
  }
  .brand__tagline {
    color: var(--brand-blue);
    font-weight: 500;
    font-size: 19px;
    margin-top: 8px;
    margin-left: 42px;
  }
  .services {
    margin-top: 26px;
    padding-top: 12px;
    border-top: 1.5px solid var(--brand-orange);
    color: var(--ink);
    font-size: 13px;
    font-weight: 600;
    letter-spacing: 2px;
    text-transform: uppercase;
  }
  .services__accent { color: var(--brand-orange); }
  .card--back {
    display: flex;
    align-items: center;
    padding: 0 48px 0 62px;
  }
  .card--back .brand__name { font-size: 38px; }
  .card--back .brand__square { width: 20px; height: 20px; }
  .card--back .brand__tagline { font-size: 13px; margin-left: 32px; margin-top: 6px; }
  .divider {
    width: 1.5px;
    height: 170px;
    background: var(--brand-orange);
    margin: 0 30px;
  }
  .contact__name {
    font-weight: 800;
    font-size: 21px;
    letter-spacing: 1.5px;
    text-transform: uppercase;
  }
  .contact__first { color: var(--brand-orange); }
  .contact__last { color: var(--brand-blue); }
  .contact__role {
    color: var(--ink);
    font-size: 14px;
    letter-spacing: 1px;
    margin: 2px 0 14px;
  }
  .contact__list { list-style: none; }
  .contact__item {
    display: flex;
    align-items: center;
    gap: 9px;
    color: var(--ink);
    font-size: 13px;
    letter-spacing: 0.6px;
    margin-bottom: 6px;
  }
  .contact__icon { width: 13px; height: 13px; flex: none; fill: var(--brand-blue); }
  .contact__note {
    margin-top: 12px;
    color: var(--brand-blue);
    font-size: 11px;
    font-weight: 600;
    letter-spacing: 0.8px;
  }
</style>
</head>
<body>
<main class="sheet">
  <section class="card card--front" aria-label="Card front">
    <div class="brand">
      <div class="brand__row">
        <span class="brand__square"></span>
        <span class="brand__name">Vextorial</span>
      </div>
      <span class="brand__tagline">developer of custom applications</span>
    </div>
    <p class="services">Custom Software <span class="services__accent">·</span> Bitcoin Services</p>
  </section>

  <section class="card card--back" aria-label="Card back">
    <div class="brand">
      <div class="brand__row">
        <span class="brand__square"></span>
        <span class="brand__name">Vextorial</span>
      </div>
      <span class="brand__tagline">developer of custom applications</span>
    </div>
    <div class="divider"></div>
    <div class="contact">
      <p class="contact__name"><span class="contact__first">Dale</span> <span class="contact__last">Parker</span></p>
      <p class="contact__role">Owner</p>
      <ul class="contact__list">
        <li class="contact__item">
          <svg class="contact__icon" viewBox="0 0 24 24" aria-hidden="true"><path d="M6.6 10.8a15.1 15.1 0 0 0 6.6 6.6l2.2-2.2c.3-.3.7-.4 1-.2 1.1.4 2.3.6 3.6.6.6 0 1 .4 1 1V20c0 .6-.4 1-1 1C10.6 21 3 13.4 3 4c0-.6.4-1 1-1h3.5c.6 0 1 .4 1 1 0 1.3.2 2.5.6 3.6.1.3 0 .7-.2 1z"/></svg>
          (888) 555-VXTRL
        </li>
        <li class="contact__item">
          <svg class="contact__icon" viewBox="0 0 24 24" aria-hidden="true"><path d="M2 5h20v14H2z"/><path d="M3 6l9 7 9-7" fill="none" stroke="#d8e2ee" stroke-width="1.6"/></svg>
          dale@vextorial.com
        </li>
        <li class="contact__item">
          <svg class="contact__icon" viewBox="0 0 24 24" aria-hidden="true"><circle cx="12" cy="12" r="10"/><path d="M2 12h20M12 2c3 3 3 17 0 20M12 2c-3 3-3 17 0 20" fill="none" stroke="#d8e2ee" stroke-width="1.4"/></svg>
          www.vextorial.com
        </li>
      </ul>
      <p class="contact__note">Bitcoin education &amp; payment integration</p>
    </div>
  </section>
</main>
</body>
</html>
```